KELBRIDGE PAINTING

We are a painting company. We paint residential, commercial and strata jobs. I need the website to be very sharp, neat and elegant. I've attached our logo. the Logo needs to be embossed as a gold color and the background like a Matt black. I need these tabs:

• HOME • ABOUT US • SERVICES • TESTIMONIALS • SHOWCASE • CONTACT US

Be creative and innovative in your style.
take this as an example to just get the gist of what I'm expecting. If you can better it then the job is yours!

http://rickhalvorpainting.com.au/contact.html

I look forward to seeing your artwork :)

#These are the links to my logo in PSD format.

https://www.filevaultzy.com/s/qwertplk83nd7ha/Kelbridge%20Painting%20Luxury%20Gold.rar

https://www.filevaultzy.com/sh/bzuyrak2m5wqp9/QoPL7-xvMn

Painting

• Making the Logo embossed like the artworks i have attached is definitely a necessity.

Can you let me know if this is possible to apply to the website.

thank you

```html
<!DOCTYPE html>
<html lang="en">
<head>
<meta charset="utf-8">
<title>Kelbridge Painting</title>
<link href="https://fonts.googleapis.com/css2?family=Source+Sans+3:ital,wght@0,400;0,600;0,700;1,400&display=swap" rel="stylesheet">
<style>
:root{
  --ink:#1e222b;
  --footer:#40444c;
  --gold:#f2c14e;
  --gold-deep:#e2ad3a;
  --gold-pale:#f3dca8;
  --caption:#9a9ca0;
  --white:#ffffff;
}
*{margin:0;padding:0;box-sizing:border-box}
html,body{width:1040px;height:1200px;overflow:hidden}
body{background:var(--ink);font-family:"Source Sans 3",sans-serif;color:var(--white);position:relative}
.header{position:absolute;left:0;top:0;width:1040px;height:80px;background:var(--ink);border-bottom:1px solid var(--gold-deep)}
.phone{position:absolute;right:144px;top:16px;display:flex;align-items:center;gap:8px;color:var(--gold);font-weight:700;font-size:20px}
.nav{position:absolute;right:144px;top:56px;display:flex;gap:26px;font-weight:600;font-size:13px;letter-spacing:.6px}
.nav span{color:var(--white)}
.nav .active{color:var(--gold)}
.hero{position:absolute;left:0;top:81px;width:1040px;height:391px;
  background:radial-gradient(ellipse at 80% 10%,#f3e6d2 0%,rgba(243,230,210,0) 30%),
  linear-gradient(180deg,#6b4a33 0%,#7d5a42 40%,#b59a8a 75%,#c6b0a6 100%)}
.brand-band{position:absolute;left:240px;top:80px;width:440px;height:35px;
  background:linear-gradient(90deg,#f0c75a,#f5d77f 60%,#eac155);display:flex;align-items:center;padding-left:15px}
.brand-name{color:var(--ink);font-weight:700;font-size:20px;letter-spacing:1px}
.brand-rule{width:1px;height:17px;background:#b68a1f;margin:0 13px}
.brand-tag{color:var(--ink);font-style:italic;font-size:15px}
.brand-mark{position:absolute;left:146px;top:18px;width:100px;height:100px;border-radius:50%;background:var(--ink)}
.dots{position:absolute;left:840px;top:107px;display:flex;gap:8px}
.dots i{width:8px;height:8px;background:#3a3e46;display:block}
.dots i.on{background:var(--gold)}
.caption-box{position:absolute;left:152px;top:299px;width:552px;height:120px;background:var(--ink);padding:14px 0 0 31px;
  font-size:38px;line-height:44px;color:var(--white)}
.accent-left{position:absolute;left:143px;top:291px;width:9px;height:47px;background:var(--gold-deep)}
.accent-grey{position:absolute;left:674px;top:299px;width:30px;height:5px;background:#8b8f96}
.accent-corner{position:absolute;left:576px;top:340px;width:144px;height:88px;border-right:16px solid var(--gold-deep);border-bottom:9px solid var(--gold-deep)}
.stripe{position:absolute;left:0;width:1040px;height:8px;display:flex}
.stripe i{display:block;height:8px}
.showcase-title{position:absolute;left:143px;top:510px;font-size:39px;font-weight:600;color:var(--gold);letter-spacing:.5px}
.tile{position:absolute;width:208px}
.tile .photo{width:208px;height:208px}
.tile .label{text-align:center;margin-top:14px;font-weight:700;font-size:15px;letter-spacing:.8px;color:var(--caption)}
.footer{position:absolute;left:0;top:1144px;width:1040px;height:56px;background:var(--footer)}
.copyright{position:absolute;left:145px;top:18px;font-size:11.5px;color:var(--white)}
.social{position:absolute;left:748px;top:15px;display:flex;gap:14px}
.social i{display:block;width:26px;height:26px;border-radius:50%;background:#cfd0d2}
</style>
</head>
<body>

<section class="hero" role="img" aria-label="Photo of a modern living room with a brown leather sectional sofa"></section>

<header class="header">
  <div class="phone">
    <svg width="18" height="18" viewBox="0 0 24 24" aria-hidden="true"><path fill="#f2c14e" d="M6.6 10.8a15.1 15.1 0 0 0 6.6 6.6l2.2-2.2c.3-.3.7-.4 1-.2 1.1.4 2.3.6 3.6.6.6 0 1 .4 1 1V20c0 .6-.4 1-1 1A17 17 0 0 1 3 4c0-.6.4-1 1-1h3.5c.6 0 1 .4 1 1 0 1.3.2 2.5.6 3.6.1.3 0 .7-.2 1z"/></svg>
    <span>1300 47 19 52</span>
  </div>
  <nav class="nav">
    <span class="active">HOME</span><span>ABOUT US</span><span>SERVICES</span><span>TESTIMONIALS</span><span>SHOWCASE</span><span>CONTACT US</span>
  </nav>
</header>

<div class="brand-mark" aria-hidden="true"></div>
<div class="brand-band">
  <span class="brand-name">KELBRIDGE PAINTING</span><span class="brand-rule"></span><span class="brand-tag">Painting Australia Everyday!</span>
</div>
<div class="dots"><i></i><i></i><i></i><i class="on"></i></div>

<div class="accent-left"></div>
<div class="accent-corner"></div>
<div class="caption-box">We paint residential,<br>commercial and strata jobs</div>
<div class="accent-grey"></div>

<div class="stripe" style="top:472px">
  <i style="width:249px;background:var(--ink)"></i><i style="width:71px;background:#4a4f58"></i><i style="width:78px;background:#6f737a"></i><i style="width:124px;background:#9a9ca0"></i><i style="width:104px;background:#d4a520"></i><i style="width:71px;background:#e3b444"></i><i style="width:78px;background:#ecc874"></i><i style="width:265px;background:var(--gold-pale)"></i>
</div>

<h2 class="showcase-title">Showcase</h2>

<div class="tile" style="left:152px;top:600px"><div class="photo" role="img" aria-label="Living room with yellow walls and fireplace" style="background:linear-gradient(160deg,#e9c23c,#d9b24a 50%,#e8e2d8)"></div><div class="label">IMAGE TEXT</div></div>
<div class="tile" style="left:416px;top:600px"><div class="photo" role="img" aria-label="Bedroom with sage green walls and padded headboard" style="background:linear-gradient(160deg,#9fb49c,#9c7a4a 45%,#e8e2c8)"></div><div class="label">IMAGE TEXT</div></div>
<div class="tile" style="left:680px;top:600px"><div class="photo" role="img" aria-label="Lounge with orange feature wall" style="background:linear-gradient(160deg,#e98a1c,#e7a04a 45%,#d8d4d0)"></div><div class="label">IMAGE TEXT</div></div>
<div class="tile" style="left:152px;top:864px"><div class="photo" role="img" aria-label="Room with grey wall and yellow column" style="background:linear-gradient(90deg,#7c7f82 50%,#f1b800 52%,#e8b400)"></div><div class="label">IMAGE TEXT</div></div>
<div class="tile" style="left:416px;top:864px"><div class="photo" role="img" aria-label="Open living area with warm yellow walls" style="background:linear-gradient(180deg,#e8d49a,#c79d3a 45%,#6b4a2c)"></div><div class="label">IMAGE TEXT</div></div>
<div class="tile" style="left:680px;top:864px"><div class="photo" role="img" aria-label="Bedroom with red orange wall" style="background:linear-gradient(160deg,#d9532a,#e3602e 50%,#f0b640)"></div><div class="label">IMAGE TEXT</div></div>

<div class="stripe" style="top:1136px">
  <i style="width:265px;background:var(--gold-pale)"></i><i style="width:70px;background:#ecc874"></i><i style="width:79px;background:#e3b444"></i><i style="width:106px;background:#d4a520"></i><i style="width:122px;background:#9a9ca0"></i><i style="width:78px;background:#6f737a"></i><i style="width:71px;background:#4a4f58"></i><i style="width:249px;background:var(--ink)"></i>
</div>

<footer class="footer">
  <p class="copyright">Copyright @ 2013 Kelbridge Painting. All rights reserved.</p>
  <div class="social" aria-hidden="true"><i></i><i></i><i></i><i></i></div>
</footer>

</body>
</html>
```